Web Design Project

We are an IT System Integrator. We provide Korvin 450 ERP System, CRM etc. We also provide hardware, networking servicing. Please look at www.zolvantix.com.sg. They provide the same service as us. We like to redesign our web site. I will attached the color that I prefer for reference.

Our website is www.tadurk.com.sg.  It has been created about 14 years ago.  We are trying to revamp it with a new look and information.   The new website must be informative, fast.    I have attached an attachment which show the color that I prefer(brownish golden).   

Our competitor (www.zolvantix.com) is carrying the same trade as us.  They have all the informations In their website that we will like to have.  Therefore I recommend you to take a look at my competitor website and have a better   
understanding on the kind of information I would like to have for my new website.

This project is guarantee to the person with the best design.  We can have it guarantee.

Target Market(s)

Corporate and companies

Industry/Entity Type

Hardware

```html
<!DOCTYPE html>
<html lang="en">
<head>
<meta charset="utf-8">
<title>Tadurk Information System</title>
<link rel="stylesheet" href="https://fonts.googleapis.com/css2?family=Arimo:wght@400;700&family=PT+Sans:wght@400;700&display=swap">
<style>
:root{
  --gold:#a9791c;
  --gold-light:#c49b3c;
  --brown:#6b4a06;
  --brown-dark:#4a3200;
  --text:#3c3c3c;
  --text-dark:#222;
  --panel:#e4e4e4;
  --page:#efefef;
  --white:#fff;
}
*{margin:0;padding:0;box-sizing:border-box}
html,body{width:1046px;height:1200px;overflow:hidden;background:var(--page)}
body{font-family:"PT Sans",Arial,sans-serif;color:var(--text);position:relative}
.abs{position:absolute}
.site-header{left:0;top:0;width:1046px;height:110px;background:var(--white)}
.brand{left:87px;top:26px;display:flex;align-items:center;gap:12px}
.brand-mark{width:46px;height:46px;border-radius:50%;background:var(--gold)}
.brand-name{font-family:"Arimo",Arial,sans-serif;font-size:17px;line-height:18px;color:var(--brown)}
.main-nav{left:469px;top:46px;display:flex;gap:0}
.main-nav a{font-family:"Arimo",Arial,sans-serif;font-size:15.5px;color:var(--text);text-decoration:none;margin-right:19px;padding-bottom:8px}
.main-nav a.active{color:var(--gold);border-bottom:2px solid var(--gold)}
.hero-band{left:0;top:110px;width:1046px;height:323px;background:linear-gradient(180deg,var(--brown) 0%,#9a6f1c 60%,var(--gold-light) 100%)}
.hero{left:87px;top:110px;width:872px;height:344px;border-radius:0 0 8px 8px;overflow:hidden;box-shadow:0 6px 8px rgba(0,0,0,.25);background:linear-gradient(90deg,#c9c4bd 0%,#dcdad6 40%,#e8e8e5 100%)}
.hero-photo{left:0;top:0;width:510px;height:344px;background:linear-gradient(90deg,#b7aca2 0%,#d4ccc4 55%,rgba(232,232,229,0) 100%)}
.hero-copy{right:34px;top:126px;text-align:right;font-family:"Arimo",Arial,sans-serif;font-weight:700;line-height:1}
.hero-copy .l1{font-size:29px;color:#6e4b0a}
.hero-copy .l2{font-size:37px;color:#5a3d07;margin-top:-2px}
.hero-copy .l3{font-size:21px;color:#5a3d07;margin-top:2px}
.hero-copy .l4{font-size:20px;color:var(--gold);margin-top:4px}
.hero-dots{left:19px;top:315px;display:flex;gap:4px}
.hero-dots span{width:13px;height:13px;border-radius:50%;background:#6b6b6b}
.hero-dots span.on{background:var(--brown)}
.panel{background:var(--panel);border-radius:7px;left:87px;width:247px}
.panel h3{font-family:"PT Sans",Arial,sans-serif;font-weight:400;font-size:15px;color:var(--gold);padding:15px 12px 10px;border-bottom:1px solid #d0d0d0;margin:0 0 0}
.news{top:525px;height:222px}
.news-item{padding:10px 12px 8px;font-size:12px;line-height:15px;border-bottom:1px solid #d0d0d0}
.news-item:last-child{border-bottom:none}
.news-item b{color:var(--text-dark);font-size:12.5px}
.call{left:87px;top:777px;width:247px;height:87px;border-radius:7px;overflow:hidden;background:linear-gradient(90deg,var(--brown-dark),#9a6c18 60%,#c9a24e)}
.call-text{left:11px;top:14px;font-family:"Arimo",Arial,sans-serif;font-weight:700;color:var(--white);font-size:21px;line-height:24px;letter-spacing:-.5px}
.call-photo{right:0;top:0;width:72px;height:87px;background:linear-gradient(180deg,#5b4a3a,#2b2630)}
.testimonials{top:890px;height:162px}
.testimonials .quote{padding:10px 12px;font-size:11.5px;line-height:15px}
.testimonials .who{font-weight:700;color:var(--text-dark);margin-top:10px}
.testimonials .src{font-size:10px;color:var(--gold)}
.welcome h1{left:362px;top:520px;font-family:"Arimo",Arial,sans-serif;font-weight:400;font-size:24px;color:var(--gold);white-space:nowrap}
.lead{left:364px;top:561px;width:596px;font-size:15px;line-height:18px;font-weight:700;color:var(--text-dark)}
.intro{left:364px;top:612px;width:410px;font-size:13px;line-height:18px;text-align:justify}
.intro a,.more{color:var(--gold);text-decoration:none}
.intro-photo{left:792px;top:612px;width:167px;height:135px;border-radius:6px;border:4px solid #f5f5f5;box-shadow:0 0 3px rgba(0,0,0,.3);background:linear-gradient(135deg,#cfe4f5,#3b7bbf 80%)}
.partners{left:366px;top:795px;width:594px;display:flex;justify-content:space-between;align-items:center}
.partner{background:#d3d3d3}
.p1{width:84px;height:30px;border-radius:15px}
.p2{width:112px;height:26px;border-radius:4px}
.p3{width:54px;height:54px;border-radius:50%}
.p4{width:62px;height:50px;border-radius:4px}
.p5{width:118px;height:32px}
.story{top:893px;width:272px}
.story h2{font-family:"Arimo",Arial,sans-serif;font-weight:400;font-size:20px;color:var(--gold);margin-bottom:10px}
.story p{font-size:13px;line-height:18.5px;border-bottom:1px solid #cfcfcf;padding-bottom:12px;height:84px}
.story .more{display:block;margin-top:12px;font-size:13px;font-weight:700}
.site-footer{left:0;top:1106px;width:1046px;height:94px;background:var(--brown);border-top:14px solid var(--brown-dark)}
.foot-nav{left:87px;top:1148px;display:flex;gap:15px}
.foot-nav a,.copyright{font-family:"Arimo",Arial,sans-serif;font-size:13px;color:var(--white);text-decoration:none}
.copyright{right:87px;top:1148px}
</style>
</head>
<body>
<header class="site-header abs">
  <div class="brand abs"><span class="brand-mark"></span><span class="brand-name">Tadurk<br>Information<br>System</span></div>
  <nav class="main-nav abs">
    <a class="active" href="#">Home</a><a href="#">Solution</a><a href="#">Hardware</a><a href="#">Services</a><a href="#">Clients</a><a href="#">About Us</a><a href="#" style="margin-right:0">Contact Us</a>
  </nav>
</header>

<div class="hero-band abs"></div>
<section class="hero abs">
  <div class="hero-photo abs" role="img" aria-label="Support staff wearing headsets in a bright office"></div>
  <div class="hero-copy abs">
    <div class="l1">Accounting software,</div>
    <div class="l2">networking,</div>
    <div class="l3">hardware maintenance</div>
    <div class="l4">and consulting assistance</div>
  </div>
  <div class="hero-dots abs"><span></span><span></span><span class="on"></span><span></span></div>
</section>

<aside class="panel news abs">
  <h3>RECENT NEWS</h3>
  <div class="news-item"><b>Aliquam bibendum pretium metus vel</b><br>Sed lacinia vulputate dolor, nec congue nunc accumsan at. Praesent leo magna,</div>
  <div class="news-item"><b>Aliquam quis mauris accumsan mauris pharetra porttitor sed non enim</b><br>Nunc vestibulum posuere sem non mollis. Phasellus tellus augue, laoreet sit amet semper eu, dignissim nec felis. Aenean iaculis risus a erat</div>
</aside>

<div class="call abs">
  <div class="call-text abs">Call us at<br>(065) 6100-4827</div>
  <div class="call-photo abs" role="img" aria-label="Businessman talking on a mobile phone"></div>
</div>

<aside class="panel testimonials abs">
  <h3>TESTIMONIALS</h3>
  <div class="quote">" The [staff at]...Tadurk Information Systems, are friendly attentive and supportive. Any problem, regardless of time, ... "
    <div class="who">-Group Data &amp; System Manager,<br>Linden Technologies Ltd</div>
    <div class="src">(Article featured in Tech Review Asia magazine, Oct 2000)</div>
  </div>
</aside>

<main class="welcome">
  <h1 class="abs">Welcome to Tadurk Information System</h1>
  <p class="lead abs">Lorem ipsum dolor sit amet, consectetur adipiscing elit. Sed id tempus enim. Etiam eros velit, rutrum in fringilla id, fermentum sit amet nulla. Nullam cursus mi ut</p>
  <p class="intro abs">Aenean dapibus lorem laoreet ante pharetra ornare malesuada orci ornare. Ut volutpat ipsum ipsum, eget suscipit mauris. Sed sed nisl ac justo rutrum convallis. Fusce facilisis, nunc et viverra iaculis, arcu augue tempor ipsum, ut auctor sapien justo ac metus. Morbi adipiscing sodales condimentum. Nunc porta hendrerit turpis, nec pharetra enim interdum id. Donec vel metus adipiscing tortor facilisis venenatis. Mauris vel volutpat leo. Nunc non justo nunc. Donec sapien arcu, egestas at facilisis et, interdum ...<a href="#">Read More</a></p>
  <div class="intro-photo abs" role="img" aria-label="Silhouettes of business people against a blue globe"></div>

  <div class="partners abs" aria-label="Partners">
    <span class="partner p1"></span><span class="partner p2"></span><span class="partner p3"></span><span class="partner p4"></span><span class="partner p5"></span>
  </div>

  <article class="story abs" style="left:366px">
    <h2>Success Stories</h2>
    <p>Aenean dapibus lorem laoreet ante pharetra ornare malesuada orci ornare. Ut volutpat ipsum ipsum, eget suscipit mauris. Sed sed nisl ac justo rutrum convallis. Fusce facilisis,</p>
    <a class="more" href="#">Read More</a>
  </article>
  <article class="story abs" style="left:683px">
    <h2>Latest Korvin</h2>
    <p>Nunc porta hendrerit turpis, nec pharetra enim interdum id. Donec vel metus adipiscing tortor facilisis venenatis. Mauris vel volutpat leo. Nunc non justo nunc.</p>
    <a class="more" href="#">Read More</a>
  </article>
</main>

<footer class="site-footer abs"></footer>
<nav class="foot-nav abs"><a href="#">Solution</a><a href="#">Hardware</a><a href="#">Services</a><a href="#">Clients</a><a href="#">About Us</a><a href="#">Contact Us</a></nav>
<div class="copyright abs">© Copyright Information 2013.</div>
</body>
</html>
```